PopGala Fundraiser

I am looking for a fresh design for the 10th annual PopGala fundraiser. Green and blue colors need to be incorporated . I attached the current flyer. I would like this flyer for September 20, 2020. This is a fundraiser to help find a cure for NF, nuerofibromatosis.
Updates

We are looking for a fresh look for the 10th annual event

Target Market(s)

Families and individuals of surrounding areas

Colors
0255a3
add136

Requirements
Must have
• Blue and green colors. It is the 10th annual. The logos of TQ CENTER and children’s hospital logo that are shown on the previous flyer I attached
Nice to have
• Eye catching

```html
<!DOCTYPE html>
<html lang="en">
<head>
<meta charset="utf-8">
<title>PopGala – 10th Annual Fundraiser</title>
<link rel="stylesheet" href="https://fonts.googleapis.com/css2?family=Roboto+Condensed:wght@300;400;700&family=Oswald:wght@600&family=Gochi+Hand&family=Roboto:wght@400;700&display=swap">
<style>
  :root {
    --white: #ffffff;
    --ink: #555555;
    --ink-dark: #333333;
    --navy: #1b2a4e;
    --title-blue: #3a3f9e;
    --icon-blue: #1079bf;
    --icon-green: #8cc63e;
    --brand-blue: #0255a3;
    --brand-green: #add136;
  }
  html, body { margin: 0; padding: 0; }
  body {
    width: 873px; height: 1200px; overflow: hidden;
    background: var(--white); position: relative;
    font-family: "Roboto Condensed", "Arial Narrow", sans-serif;
    color: var(--ink);
  }
  .splash { position: absolute; left: 0; top: 0; width: 873px; height: 460px; }
  .event-info { position: absolute; left: 0; top: 463px; width: 873px; text-align: center;
    font-weight: 300; font-size: 27px; line-height: 37px; color: var(--ink); }
  .event-info .row { display: flex; justify-content: center; align-items: center; gap: 8px; }
  .event-info svg { width: 27px; height: 27px; }
  .features { position: absolute; left: 0; top: 603px; width: 873px; height: 140px; }
  .feature { position: absolute; width: 170px; text-align: center; }
  .feature svg { width: 104px; height: 104px; display: block; margin: 0 auto; }
  .feature-label { font-weight: 700; font-size: 36px; line-height: 40px; color: var(--ink); margin-top: 2px; }
  .activities { position: absolute; left: 0; top: 755px; width: 873px; text-align: center;
    font-family: "Gochi Hand", cursive; font-size: 31px; line-height: 45px; color: var(--ink-dark); }
  .activities .studio { font-family: "Gochi Hand", cursive; color: var(--ink-dark); }
  .web-link { position: absolute; left: 0; top: 948px; width: 873px; text-align: center;
    font-family: "Roboto", sans-serif; font-weight: 700; font-size: 17px; color: var(--ink-dark); }
  .web-link svg { width: 18px; height: 18px; vertical-align: -3px; margin-right: 4px; }
  .donate-note { position: absolute; left: 0; top: 975px; width: 873px; text-align: center;
    font-family: "Roboto", sans-serif; font-size: 14px; color: var(--ink); }
  .partner-left { position: absolute; left: 66px; top: 1040px; width: 140px; text-align: center;
    font-family: "Roboto Condensed", sans-serif; font-weight: 700; font-size: 34px; line-height: 36px; color: var(--navy); }
  .partner-right { position: absolute; left: 630px; top: 1050px; width: 200px; text-align: center;
    font-family: "Roboto Condensed", sans-serif; font-weight: 700; font-size: 30px; line-height: 34px; color: var(--navy); }
  .contacts { position: absolute; left: 276px; top: 1018px; display: flex; gap: 10px; align-items: center; }
  .contacts svg { width: 34px; height: 30px; }
  .contact-list { font-family: "Roboto Condensed", sans-serif; font-weight: 700; font-size: 15px; line-height: 21px; color: var(--ink-dark);
    display: grid; grid-template-columns: auto auto; column-gap: 6px; }
  .footer { position: absolute; left: 0; top: 1155px; width: 873px; text-align: center;
    font-family: "Roboto", sans-serif; font-size: 12px; line-height: 20px; color: var(--ink); }
  .footer strong { color: var(--ink-dark); }
</style>
</head>
<body>

<svg class="splash" viewBox="0 0 873 460" aria-labelledby="event-title">
  <defs>
    <linearGradient id="rainbow" x1="0" y1="0" x2="1" y2="0">
      <stop offset="0" stop-color="#e3262a"/>
      <stop offset="0.2" stop-color="#f47a20"/>
      <stop offset="0.38" stop-color="#f9e51c"/>
      <stop offset="0.58" stop-color="#9fcf3a"/>
      <stop offset="0.78" stop-color="#139a8c"/>
      <stop offset="1" stop-color="#2c3796"/>
    </linearGradient>
    <filter id="soft"><feGaussianBlur stdDeviation="6"/></filter>
  </defs>
  <g role="img" aria-label="Rainbow watercolour splash background">
    <path filter="url(#soft)" fill="url(#rainbow)"
      d="M40 120 C80 70 140 90 190 60 C260 30 330 70 400 40 C480 10 560 50 630 30 C700 15 780 50 840 80
         C870 130 860 190 850 240 C860 300 820 340 770 350 C700 370 640 345 580 380 C520 420 470 440 430 400
         C380 360 330 380 270 370 C200 360 150 380 100 340 C50 310 30 260 25 210 C20 170 25 145 40 120 Z"/>
  </g>
  <text x="136" y="290" transform="rotate(-90 136 290)" font-family="Oswald, sans-serif" font-weight="600"
        font-size="19" fill="#ffffff" textLength="146">10TH ANNUAL</text>
  <text id="event-title" x="158" y="290" font-family="Oswald, sans-serif" font-weight="600" font-size="232"
        textLength="596" lengthAdjust="spacingAndGlyphs" fill="#ffffff">PO<tspan fill="#3a3f9e">PG</tspan>ALA</text>
  <text x="436" y="333" text-anchor="middle" font-family="Roboto Condensed, sans-serif" font-weight="700"
        font-size="20" fill="#ffffff">JOIN OUR RAGE DONATE AGAINST NEUROFIBROMATOSIS</text>
</svg>

<section class="event-info">
  <div class="row">
    <svg viewBox="0 0 24 24" fill="none" stroke="#666" stroke-width="1.2"><rect x="2" y="4" width="20" height="18"/><line x1="2" y1="9" x2="22" y2="9"/><line x1="7" y1="2" x2="7" y2="6"/><line x1="17" y1="2" x2="17" y2="6"/></svg>
    <span>Sunday, September 20, 2020</span>
    <svg viewBox="0 0 24 24" fill="none" stroke="#666" stroke-width="1.2"><circle cx="12" cy="13" r="9"/><polyline points="12,8 12,13 15,15"/><line x1="9" y1="2" x2="15" y2="2"/></svg>
    <span>12pm - 6pm</span>
  </div>
  <div class="row">Ridgeway County Fair Grounds</div>
  <div class="row">
    <svg viewBox="0 0 24 24" fill="none" stroke="#666" stroke-width="1.2"><path d="M12 22 C7 15 5 12 5 9 a7 7 0 0 1 14 0 c0 3-2 6-7 13z"/><circle cx="12" cy="9" r="2.5"/></svg>
    <span>214 W. Meadow Rd, Oakvale, IL 62400</span>
  </div>
</section>

<section class="features">
  <div class="feature" style="left:100px">
    <svg viewBox="0 0 104 104"><path d="M8 52 A44 44 0 0 1 70 12" fill="none" stroke="#1079bf" stroke-width="1.5"/><circle cx="52" cy="54" r="40" fill="#1079bf"/>
      <g stroke="#fff" stroke-width="3" fill="none" stroke-linecap="round"><line x1="36" y1="38" x2="68" y2="72"/><line x1="68" y1="36" x2="36" y2="72"/><line x1="62" y1="32" x2="72" y2="42"/></g></svg>
    <div class="feature-label">FOOD</div>
  </div>
  <div class="feature" style="left:270px">
    <svg viewBox="0 0 104 104"><path d="M8 52 A44 44 0 0 1 70 12" fill="none" stroke="#8cc63e" stroke-width="1.5"/><circle cx="52" cy="54" r="40" fill="#8cc63e"/>
      <g stroke="#fff" stroke-width="2.5" fill="none"><path d="M32 32 h18 c0 14-4 20-9 20 s-9-6-9-20z"/><line x1="41" y1="52" x2="41" y2="72"/><line x1="34" y1="72" x2="48" y2="72"/><path d="M54 52 h16 l-3 20 h-10z"/></g></svg>
    <div class="feature-label">DRINKS</div>
  </div>
  <div class="feature" style="left:437px">
    <svg viewBox="0 0 104 104"><path d="M8 52 A44 44 0 0 1 70 12" fill="none" stroke="#1079bf" stroke-width="1.5"/><circle cx="52" cy="54" r="40" fill="#1079bf"/>
      <g stroke="#fff" stroke-width="2.5" fill="none"><ellipse cx="40" cy="68" rx="6" ry="4"/><ellipse cx="64" cy="62" rx="6" ry="4"/><polyline points="46,68 46,38 70,32 70,62"/></g></svg>
    <div class="feature-label">MUSIC</div>
  </div>
  <div class="feature" style="left:599px">
    <svg viewBox="0 0 104 104" role="img" aria-label="Theatre masks icon"><path d="M8 52 A44 44 0 0 1 70 12" fill="none" stroke="#8cc63e" stroke-width="1.5"/><circle cx="52" cy="54" r="40" fill="#8cc63e"/></svg>
    <div class="feature-label">FUN</div>
  </div>
</section>

<section class="activities">
  <div>Kids Games, Bounce Houses, Face Painting</div>
  <div>Silent &amp; Live Auction, Bake Sale, Raffes</div>
  <div>Children's Special <span class="studio">Larkfield Photo</span> by 12-2 Walk-in-Appts.</div>
</section>

<div class="web-link"><svg viewBox="0 0 24 24" fill="none" stroke="#555" stroke-width="1.4"><circle cx="12" cy="12" r="10"/><ellipse cx="12" cy="12" rx="4" ry="10"/><line x1="2" y1="12" x2="22" y2="12"/></svg>http/example.com/popgala. K.E.L.S.E.Y</div>
<div class="donate-note">If anyone wishes to donate any items or purcahse a ticket please contact one of the following people:</div>

<div class="partner-left">TQ<br>CENTER</div>

<div class="contacts">
  <svg viewBox="0 0 34 30" fill="none" stroke="#666" stroke-width="1.3"><path d="M3 10 c0-6 28-6 28 0 v3 h-7 v-3 h-14 v3 h-7z"/><path d="M8 14 h18 l3 12 h-24z"/><circle cx="17" cy="20" r="3"/></svg>
  <div class="contact-list">
    <span>Dana Price</span><span>: (618) 555-0141</span>
    <span>Carla Benton</span><span>: (217) 555-0172</span>
    <span>Mia Harlow</span><span>: (618) 555-0196</span>
    <span>Tess Morrow</span><span>: (618) 555-0116</span>
  </div>
</div>

<div class="partner-right">Maple Kids Hospital</div>

<footer class="footer">
  <div>All processed donated to Maple Kids Hospital Lakeshore University TQ Center to help find a cure!</div>
  <div>Sponsored by Family &amp; Friends of <strong>K.E.L.S.E.Y</strong></div>
</footer>

</body>
</html>
```